Website Design for Solar Panel Company

We are working with a company called VoltaNix.

Some sites to use for content/competitors and inspiration:
https://www.brivaloo.com
https://prod.aws-prod.kelmatrix.com
https://tovarqueworks.net
https://www.quorvex.com/solarpanels

Thank you for taking the time to consider designing a website for us. We are web developers based in Stockton, CA, USA. Most of our projects go through the same process. Understanding this process may help you win a project with us. We custom-code all of our websites in-house. We don’t have any requirements as to what tools you use for your design, but we prefer Figma files. For any design that we label as four-stars, we send it to the client for review. The client picks the final design they want us to use. Once we complete this process, we will continue to show additional clients all the four-star sites and purchase them later. Your designs will have multiple chances to sell. For better chances of success, we ask that you follow these guidelines.

IMAGES:
If you use any images or icons in the design, we ask that you have a link to the asset so we can purchase the image/icon. Most of the designs we submit do not have the customer’s images on them unless they have some great images. Be creative; show us the feeling you are trying to portray with your image choices. Use any royalty-free site you choose. We subscribe to Pendrel and mainly use their images, but we can purchase images outside of Pendrel. PLEASE NOTE: we will not submit designs to clients with watermarks on the images.

FONTS:
We ask that you identify the fonts used in the design. This can be done in a message if you want. We typically use Google Fonts and Pendrel Fonts.

CONTENT:
We're always open to different content and ideas. We often submit designs with stock images so the client can see our vision. We typically take pictures after the website launch to use their images with our vision. Lorem Ipsum is fine for paragraphs, but we ask that you write the headers in correct English. We want to be able to show the vision and identify the sections of the website.

INSPIRATION:
We typically add a couple of links in the brief of websites we like to help you get started in your design.

REVISIONS:
We do not often ask for revisions of the designs unless we see something in the design that may not appeal to the client. If there are slight changes that we want to make, we do that in the development process.

FEEDBACK:
We rarely give feedback on designs during the design process. We are working on many website projects and do not have the time to provide feedback. We usually respond if your request is well thought out and asks specific questions, but a note asking “feedback, please” usually goes unanswered.

```html
<!DOCTYPE html>
<html lang="en">
<head>
<meta charset="utf-8">
<title>VoltaNix – Solar Energy</title>
<link href="https://fonts.googleapis.com/css2?family=Open+Sans:wght@400;600;700&family=Tinos:wght@400;700&display=swap" rel="stylesheet">
<style>
:root{
  --green:#7dc127;
  --navy:#1e3a6e;
  --navy-deep:#1d3f78;
  --ink:#2b2f38;
  --muted:#7a7f8a;
  --lavender:#eeebf5;
  --lavender-2:#e4def0;
  --dark:#1f2733;
  --white:#ffffff;
}
*{margin:0;padding:0;box-sizing:border-box}
html,body{width:1200px;height:5068px;overflow:hidden}
body{position:relative;background:var(--white);font-family:"Open Sans",sans-serif;color:var(--ink)}
h1,h2,h3,h4{font-weight:400}
.abs{position:absolute}
.serif{font-family:"Tinos",serif}
.photo{position:absolute}
.section-title{position:absolute;left:0;width:1200px;text-align:center;font-family:"Tinos",serif;font-size:46px;color:var(--navy);font-weight:400}
.section-sub{position:absolute;left:0;width:1200px;text-align:center;font-size:13px;line-height:24px;color:var(--muted)}

/* header */
.topbar-item{position:absolute;top:20px;display:flex;align-items:center;gap:10px;font-size:10px;line-height:13px}
.topbar-item b{font-size:11px}
.round-icon{width:28px;height:28px;border-radius:50%;background:var(--navy);display:flex;align-items:center;justify-content:center}
.brand{position:absolute;left:470px;top:28px;width:240px;text-align:center;font-weight:700;font-size:42px;color:var(--ink);letter-spacing:1px}
.btn-book{position:absolute;left:880px;top:12px;width:182px;height:38px;border-radius:19px;background:var(--navy);color:#fff;font-size:11px;font-weight:700;display:flex;align-items:center;justify-content:center}
.nav a{position:absolute;top:86px;font-size:11px;color:#555;text-decoration:none}
.nav .rule{position:absolute;top:68px;height:1px;background:#ddd}

/* hero */
.hero{left:0;top:120px;width:1200px;height:780px;background:
  radial-gradient(ellipse 180px 220px at 62% 30%,rgba(178,190,96,.45),rgba(178,190,96,0) 70%),
  radial-gradient(ellipse 500px 300px at 85% 10%,rgba(150,165,178,.55),rgba(150,165,178,0) 70%),
  linear-gradient(180deg,#56636f 0%,#3d4a58 30%,#2f4158 55%,#24344a 75%,#1c2633 100%)}
.hero-eyebrow{left:82px;top:362px;color:#fff;font-weight:700;font-size:19px;letter-spacing:6px}
.hero-title{left:76px;top:410px;color:#fff;font-weight:700;font-size:46px;letter-spacing:1px}
.hero-line{left:78px;top:492px;width:702px;height:2px;background:#fff}
.hero-text{left:82px;top:522px;width:640px;color:#fff;font-size:15px;line-height:28px}
.btn{position:absolute;height:38px;border-radius:19px;font-size:13px;font-weight:700;display:flex;align-items:center;justify-content:center}

/* about */
.about-kicker{left:620px;top:976px;color:var(--green);font-family:"Tinos",serif;font-size:16px}
.about-title{left:620px;top:1012px;width:520px;font-family:"Tinos",serif;font-weight:400;font-size:35px;line-height:52px;color:var(--navy)}
.about-quote{left:620px;top:1130px;width:470px;border-left:2px solid var(--navy);padding-left:14px;font-size:13px;line-height:24px;color:var(--muted)}
.about-body{left:620px;top:1210px;width:470px;font-size:13px;line-height:24px;color:var(--muted)}

/* services */
.service-card{position:absolute;top:1750px;width:320px;height:268px;border-radius:6px;overflow:hidden}
.service-card .shade{position:absolute;inset:0;background:linear-gradient(180deg,rgba(20,28,40,.25),rgba(20,28,40,.05) 45%,rgba(20,28,40,.45))}
.service-card h3{position:absolute;left:20px;top:64px;font-family:"Tinos",serif;font-weight:700;font-size:29px;color:#fff}
.service-card .arrow{position:absolute;left:42px;top:206px}
.service-icon{position:absolute;top:1716px;width:68px;height:68px;border-radius:50%;background:#fff;display:flex;align-items:center;justify-content:center;box-shadow:0 2px 8px rgba(0,0,0,.15)}

/* projects */
.frame{position:absolute;border:8px solid #fff;background:#fff}
.carousel-btn{position:absolute;width:52px;height:52px;border-radius:50%;background:#fff;box-shadow:0 2px 8px rgba(0,0,0,.25);display:flex;align-items:center;justify-content:center}

/* why */
.why-title{position:absolute;font-family:"Tinos",serif;font-size:23px;color:var(--navy)}
.why-text{position:absolute;width:250px;font-size:13px;line-height:24px;color:var(--muted)}
.why-icon{position:absolute;width:84px;height:84px;border-radius:50%;background:var(--navy);border:5px solid #fff;box-shadow:0 0 0 3px var(--green);display:flex;align-items:center;justify-content:center}

/* hours + form */
.hours{left:0;top:3360px;width:1200px;height:565px;background:
  radial-gradient(ellipse 700px 160px at 40% 68%,rgba(196,122,58,.35),rgba(196,122,58,0) 70%),
  linear-gradient(180deg,#1a2230 0%,#232c39 45%,#3b3530 72%,#2a2e34 100%)}
.hours-title{left:93px;top:3495px;color:#fff;font-family:"Tinos",serif;font-weight:400;font-size:28px}
.hours-table{left:93px;top:3565px;width:495px;height:235px;border-left:5px solid var(--green);background:rgba(20,26,34,.7);padding:10px 34px}
.hours-row{display:flex;justify-content:space-between;height:51px;align-items:center;border-bottom:1px solid rgba(255,255,255,.15);font-size:14px;color:#fff}
.hours-row:last-child{border-bottom:none}
.hours-row span:first-child{font-weight:600}
.hours-row span:last-child{color:#d5d7dc}
.form-card{left:612px;top:3390px;width:491px;height:495px;background:var(--lavender-2)}
.field{position:absolute;height:50px;background:#fff;font-size:13px;color:#444;display:flex;align-items:center;padding-left:28px}

/* reviews */
.review-card{position:absolute;top:4200px;width:320px;height:268px;background:#fff;box-shadow:0 4px 18px rgba(0,0,0,.1)}
.review-card .avatar{position:absolute;left:30px;top:-34px;width:64px;height:64px;border-radius:50%;border:3px solid #fff;background:linear-gradient(160deg,#e9e3dc,#b68c6c 60%,#6b4c3a)}
.review-card .quote{position:absolute;right:34px;top:-18px;font-family:"Tinos",serif;font-weight:700;font-size:110px;line-height:110px;color:var(--green);opacity:.7}
.review-card .stars{position:absolute;left:26px;top:58px;color:#f06a1d;font-size:15px;letter-spacing:3px}
.review-card p{position:absolute;left:26px;top:86px;width:270px;font-size:12px;line-height:23px;color:var(--muted)}
.review-card h4{position:absolute;left:26px;top:178px;font-family:"Tinos",serif;font-weight:400;font-size:20px;color:var(--ink)}
.review-card small{position:absolute;left:26px;top:212px;font-size:9px;font-weight:600;color:#8a5ab5}

/* footer */
.footer{left:0;top:4530px;width:1200px;height:485px;background:var(--dark)}
.footer-brand{left:0;top:4712px;width:1200px;text-align:center;color:#fff;font-weight:700;font-size:54px;letter-spacing:2px}
.footer-nav a{position:absolute;top:4832px;color:#fff;font-size:13px;text-decoration:none}
.footer-contact{position:absolute;top:4922px;display:flex;align-items:center;gap:12px;color:#fff;font-size:11px;line-height:17px}
.footer-contact .ring{width:58px;height:58px;border-radius:50%;border:1px solid #fff;display:flex;align-items:center;justify-content:center}
.bottom-bar{left:0;top:5015px;width:1200px;height:53px;background:var(--navy-deep)}
.social{position:absolute;top:5030px;width:24px;height:24px;border:1px solid #fff;background:rgba(255,255,255,.08)}
</style>
</head>
<body>

<!-- Header -->
<div class="topbar-item" style="left:123px">
  <div class="round-icon"><svg width="14" height="14" viewBox="0 0 24 24" fill="#fff"><path d="M6.6 10.8a15 15 0 0 0 6.6 6.6l2.2-2.2c.3-.3.7-.4 1-.2 1.1.4 2.3.6 3.6.6.6 0 1 .4 1 1V20c0 .6-.4 1-1 1C10.6 21 3 13.4 3 4c0-.6.4-1 1-1h3.5c.6 0 1 .4 1 1 0 1.3.2 2.5.6 3.6.1.3 0 .7-.2 1z"/></svg></div>
  <div><b>Call Us:</b><br>(555)014-2290</div>
</div>
<div class="topbar-item" style="left:280px">
  <div class="round-icon"><svg width="14" height="14" viewBox="0 0 24 24" fill="none" stroke="#fff" stroke-width="2"><rect x="3" y="5" width="18" height="14" rx="1"/><path d="M3 6l9 7 9-7"/></svg></div>
  <div><b>Email:</b><br>office@voltanix.com</div>
</div>
<div class="brand">VoltaNix</div>
<div class="btn-book">BOOK APPOINTMENT</div>
<nav class="nav">
  <span class="rule" style="left:110px;width:372px"></span>
  <span class="rule" style="left:700px;width:380px"></span>
  <a style="left:125px">Home</a>
  <a style="left:237px">About Us</a>
  <a style="left:387px">Services</a>
  <a style="left:706px">Team</a>
  <a style="left:833px">Blog</a>
  <a style="left:958px">Contact Us</a>
</nav>

<!-- Hero -->
<div class="photo hero" role="img" aria-label="Technician in a safety vest installing rooftop solar panels at dusk"></div>
<svg class="abs" style="left:0;top:760px" width="1200" height="160" viewBox="0 0 1200 160"><path d="M0 20 Q600 200 1200 20 L1200 160 L0 160Z" fill="#fff"/></svg>
<div class="abs hero-eyebrow">Welcome</div>
<h1 class="abs hero-title">For a sustainable tomorrow</h1>
<div class="abs hero-line"></div>
<p class="abs hero-text">Lorem ipsum dolor sit amet, consectetur adipiscing elit, sed do eiusmod tempor incididunt ut labore et dolore magna</p>
<div class="btn" style="left:82px;top:612px;width:146px;background:var(--green);color:#fff">LEARN MORE</div>
<div class="btn" style="left:240px;top:612px;width:178px;background:#fff;color:var(--ink)">REQUEST QUOTE</div>

<!-- Divider with power icon -->
<svg class="abs" style="left:230px;top:850px" width="740" height="50" viewBox="0 0 740 50"><path d="M5 10 Q370 50 735 10" fill="none" stroke="var(--green)" stroke-width="3"/></svg>
<div class="abs" style="left:568px;top:858px;width:64px;height:64px;border-radius:50%;background:#fff;box-shadow:0 2px 8px rgba(0,0,0,.2);display:flex;align-items:center;justify-content:center">
  <svg width="40" height="40" viewBox="0 0 40 40"><circle cx="20" cy="20" r="19" fill="var(--green)"/><path d="M14 13a10 10 0 1 0 12 0" fill="none" stroke="#fff" stroke-width="3" stroke-linecap="round"/><path d="M20 9v11" stroke="#fff" stroke-width="3" stroke-linecap="round"/></svg>
</div>

<!-- About -->
<svg class="abs" style="left:80px;top:955px" width="480" height="480" viewBox="0 0 480 480"><path d="M40 150 A225 225 0 1 1 240 465" fill="none" stroke="var(--green)" stroke-width="6"/></svg>
<div class="photo" style="left:95px;top:985px;width:440px;height:440px;border-radius:50%;background:
  radial-gradient(ellipse 110px 200px at 28% 65%,rgba(52,60,78,.75),rgba(52,60,78,0) 75%),
  linear-gradient(172deg,#d9dcdf 0%,#b8bec4 28%,#7f91a6 42%,#4d6784 58%,#3a5270 74%,#56647a 100%)" role="img" aria-label="Couple embracing while looking at solar panels on their home"></div>
<div class="abs about-kicker">About Us</div>
<h2 class="abs about-title">Solar Energy: Powering Homes, Empowering Lives</h2>
<p class="abs about-quote">Lorem ipsum dolor sit amet, consectetur adipiscing elit, sed do eiusmod or incididunt ut labore et dolore</p>
<p class="abs about-body">Lorem ipsum dolor sit amet, consectetur adipiscing elit, sed do eiusmod obgr incididunt ut labore et dolore Lorem ipsum dolor sit amet, consectetur adip iscing elit, sed do eiusmod tempor incididunt ut labore et dolore m agna aliqua. Ut enim ad minim veniam, quis nostrud exercitation ullamco laboris nisi ut aliquip ex ea commodo consequat.</p>
<div class="btn" style="left:620px;top:1360px;width:155px;border-radius:0;background:var(--green);color:#fff;gap:14px">Contact us <svg width="18" height="12" viewBox="0 0 18 12"><path d="M1 6h15M11 1l5 5-5 5" fill="none" stroke="#fff" stroke-width="1.6"/></svg></div>

<!-- Services -->
<div class="abs" style="left:0;top:1510px;width:1200px;height:575px;background:var(--lavender)"></div>
<h2 class="section-title" style="top:1562px">Our Services</h2>
<p class="section-sub" style="top:1628px">Lorem ipsum dolor sit amet, consectetur adipiscing elit, sed do eiusmod temp<br>or incididunt ut labore et dolore</p>

<div class="service-card" style="left:90px"><div class="photo" style="inset:0;background:linear-gradient(168deg,#c7d3dc 0%,#c9ab8e 25%,#a8674a 45%,#3c4d66 65%,#26344a 100%)" role="img" aria-label="Workers installing panels on a tiled roof"></div><div class="shade"></div><h3>Panel Installation</h3><svg class="arrow" width="48" height="20" viewBox="0 0 48 20"><path d="M2 10h42M36 3l8 7-8 7" fill="none" stroke="#fff" stroke-width="1.5"/></svg></div>
<div class="service-card" style="left:437px"><div class="photo" style="inset:0;background:linear-gradient(168deg,#8fb2d2 0%,#a9bfd2 22%,#5c7895 42%,#2b4262 65%,#1d2d45 100%)" role="img" aria-label="Engineer assessing a solar panel site"></div><div class="shade"></div><h3>Site Assessment</h3><svg class="arrow" width="48" height="20" viewBox="0 0 48 20"><path d="M2 10h42M36 3l8 7-8 7" fill="none" stroke="#fff" stroke-width="1.5"/></svg></div>
<div class="service-card" style="left:785px"><div class="photo" style="inset:0;background:linear-gradient(168deg,#cdd8e2 0%,#a9b6c3 30%,#4a5d78 52%,#8a4b3a 75%,#5a3429 100%)" role="img" aria-label="Installer carrying a panel for a battery backup system"></div><div class="shade"></div><h3>Battery Backup</h3><svg class="arrow" width="48" height="20" viewBox="0 0 48 20"><path d="M2 10h42M36 3l8 7-8 7" fill="none" stroke="#fff" stroke-width="1.5"/></svg></div>

<div class="service-icon" style="left:136px"><svg width="30" height="30" viewBox="0 0 24 24" fill="none" stroke="var(--green)" stroke-width="1.5"><path d="M12 3l2.7 5.6 6.1.9-4.4 4.3 1 6.1L12 17l-5.4 2.9 1-6.1L3.2 9.5l6.1-.9z"/></svg></div>
<div class="service-icon" style="left:483px"><svg width="30" height="30" viewBox="0 0 24 24" fill="none" stroke="var(--green)" stroke-width="1.5"><circle cx="10" cy="6" r="3"/><path d="M4 20l4-9h4l3 5M3 21h18"/></svg></div>
<div class="service-icon" style="left:832px"><svg width="30" height="30" viewBox="0 0 24 24" fill="none" stroke="var(--green)" stroke-width="1.5"><circle cx="8" cy="8" r="3"/><circle cx="16" cy="8" r="3"/><path d="M3 19c0-4 2.5-6 5-6s5 2 5 6M11 19c0-4 2.5-6 5-6s5 2 5 6"/></svg></div>

<!-- Recent Projects -->
<div class="abs" style="left:0;top:2085px;width:1200px;height:350px;background:var(--green)"></div>
<h2 class="section-title" style="top:2138px;color:#fff">Recent Projects</h2>
<p class="section-sub" style="top:2205px;color:#f0f7e6">Lorem ipsum dolor sit amet, consectetur adipiscing elit, sed do eiusmod temp<br>or incididunt ut labore et dolore</p>
<div class="frame" style="left:120px;top:2305px;width:208px;height:290px"><div class="photo" style="inset:0;background:radial-gradient(circle at 62% 38%,#fffbe6 0,#ffd27a 10%,#f08a3a 24%,rgba(120,110,140,.9) 48%,#2c4a86 68%,#1a2f62 100%)" role="img" aria-label="Solar panels under a bright sun"></div></div>
<div class="frame" style="left:879px;top:2305px;width:198px;height:290px"><div class="photo" style="inset:0;background:linear-gradient(165deg,#4e6d38 0%,#6f8a52 25%,#9aa2a8 45%,#3b5072 65%,#24375a 100%)" role="img" aria-label="Panels on a roof among trees"></div></div>
<div class="frame" style="left:315px;top:2275px;width:572px;height:350px;box-shadow:0 4px 14px rgba(0,0,0,.15)"><div class="photo" style="inset:0;background:linear-gradient(168deg,#e4e7ea 0%,#cfc2ad 18%,#a98d6e 30%,#4a5f80 42%,#2c3f5e 62%,#9c5a34 82%,#b9693e 100%)" role="img" aria-label="Solar array on a terracotta tiled roof"></div></div>
<div class="carousel-btn" style="left:292px;top:2432px"><svg width="14" height="14" viewBox="0 0 14 14"><path d="M9 2L4 7l5 5" fill="none" stroke="#111" stroke-width="2.4"/></svg></div>
<div class="carousel-btn" style="left:855px;top:2432px"><svg width="14" height="14" viewBox="0 0 14 14"><path d="M5 2l5 5-5 5" fill="none" stroke="#111" stroke-width="2.4"/></svg></div>

<!-- Why Choose Us -->
<h2 class="section-title" style="top:2686px">Why Choose Us</h2>
<p class="section-sub" style="top:2753px">Lorem ipsum dolor sit amet, consectetur adipiscing elit, sed do eiusmod temp<br>or incididunt ut labore et dolore</p>
<svg class="abs" style="left:130px;top:2860px" width="940" height="440" viewBox="0 0 940 440"><defs><linearGradient id="fadeL" x1="0" x2="1"><stop offset="0" stop-color="#fff"/><stop offset="1" stop-color="#e8e3f1"/></linearGradient><linearGradient id="fadeR" x1="1" x2="0"><stop offset="0" stop-color="#fff"/><stop offset="1" stop-color="#e8e3f1"/></linearGradient></defs><path d="M0 10 H330 A215 215 0 0 1 330 430 H0Z" fill="url(#fadeL)"/><path d="M940 10 H610 A215 215 0 0 0 610 430 H940Z" fill="url(#fadeR)"/></svg>
<div class="photo" style="left:420px;top:2840px;width:360px;height:455px;border-radius:180px;background:
  radial-gradient(ellipse 90px 110px at 50% 22%,rgba(196,150,120,.55),rgba(196,150,120,0) 80%),
  linear-gradient(180deg,#eef0f2 0%,#e3e5e8 22%,#9aa2ab 42%,#6f7882 62%,#4b535c 100%)" role="img" aria-label="Smiling businessman in a grey suit with arms crossed"></div>

<div class="why-title" style="right:822px;top:2906px">Quality Assurance</div>
<div class="why-text" style="left:128px;top:2940px;text-align:right">Lorem ipsum dolor sit amet, conser adi or incididunt ut labore et dolore</div>
<div class="why-title" style="right:822px;top:3037px">Proven Record</div>
<div class="why-text" style="left:128px;top:3071px;text-align:right">Lorem ipsum dolor sit amet, conser adi or incididunt ut labore et dolore</div>
<div class="why-title" style="right:822px;top:3171px">Personalized Approach</div>
<div class="why-text" style="left:128px;top:3205px;text-align:right">Lorem ipsum dolor sit amet, conser adi or incididunt ut labore et dolore</div>

<div class="why-icon" style="left:399px;top:2903px"><svg width="28" height="28" viewBox="0 0 24 24" fill="none" stroke="#fff" stroke-width="1.6"><path d="M4 14a8 8 0 0 1 16 0M4 14v4h3v-5H4M20 14v4h-3v-5h3"/></svg></div>
<div class="why-icon" style="left:399px;top:3038px"><svg width="28" height="28" viewBox="0 0 24 24" fill="none" stroke="#fff" stroke-width="1.6"><path d="M12 3l2.7 5.6 6.1.9-4.4 4.3 1 6.1L12 17l-5.4 2.9 1-6.1L3.2 9.5l6.1-.9z"/></svg></div>
<div class="why-icon" style="left:399px;top:3173px"><svg width="28" height="28" viewBox="0 0 24 24" fill="none" stroke="#fff" stroke-width="1.6"><circle cx="10" cy="6" r="3"/><path d="M4 20l4-9h4l3 5M3 21h18"/></svg></div>
<div class="why-icon" style="left:692px;top:2903px"><svg width="28" height="28" viewBox="0 0 24 24" fill="none" stroke="#fff" stroke-width="1.6"><circle cx="8" cy="8" r="3"/><circle cx="16" cy="8" r="3"/><path d="M3 19c0-4 2.5-6 5-6s5 2 5 6M11 19c0-4 2.5-6 5-6s5 2 5 6"/></svg></div>
<div class="why-icon" style="left:692px;top:3038px"><svg width="28" height="28" viewBox="0 0 24 24" fill="none" stroke="#fff" stroke-width="1.6"><circle cx="12" cy="13" r="8"/><path d="M12 13l4-4"/></svg></div>
<div class="why-icon" style="left:692px;top:3173px"><svg width="28" height="28" viewBox="0 0 24 24" fill="none" stroke="#fff" stroke-width="1.6"><path d="M20 12a8 8 0 0 1-14 5M4 12a8 8 0 0 1 14-5M18 3v4h-4M6 21v-4h4"/></svg></div>

<div class="why-title" style="left:797px;top:2906px">Comprehensive Services</div>
<div class="why-text" style="left:797px;top:2940px">Lorem ipsum dolor sit amet, conser adi or incididunt ut labore et dolore</div>
<div class="why-title" style="left:797px;top:3037px">Professionalism</div>
<div class="why-text" style="left:797px;top:3071px">Lorem ipsum dolor sit amet, conser adi or incididunt ut labore et dolore</div>
<div class="why-title" style="left:797px;top:3171px">Experience and Expertise</div>
<div class="why-text" style="left:797px;top:3205px">Lorem ipsum dolor sit amet, conser adi or incididunt ut labore et dolore</div>

<!-- Opening hours & appointment -->
<div class="photo hours" role="img" aria-label="Solar farm at sunset, darkened"></div>
<h3 class="abs hours-title">Opening Hours</h3>
<div class="abs hours-table">
  <div class="hours-row"><span>Monday - Thursday</span><span>08am - 05pm</span></div>
  <div class="hours-row"><span>Saturday</span><span>08am - 02pm</span></div>
  <div class="hours-row"><span>Phone</span><span>+123 456 7890</span></div>
  <div class="hours-row"><span>Email</span><span>info@company.com</span></div>
</div>
<div class="abs form-card"></div>
<div class="abs" style="left:669px;top:3430px;width:48px;height:48px;border-radius:50%;background:var(--navy);display:flex;align-items:center;justify-content:center"><svg width="24" height="24" viewBox="0 0 24 24" fill="none" stroke="#fff" stroke-width="1.5"><rect x="3" y="5" width="18" height="15" rx="1"/><path d="M3 10h18M8 3v4M16 3v4"/></svg></div>
<div class="abs" style="left:733px;top:3426px;font-size:13px;color:#333">Get in touch with us any day any time</div>
<div class="abs serif" style="left:733px;top:3448px;font-size:32px;color:var(--ink)">Make Appointment</div>
<div class="field" style="left:665px;top:3520px;width:183px">First Name</div>
<div class="field" style="left:867px;top:3520px;width:183px">Last Name</div>
<div class="field" style="left:665px;top:3593px;width:183px">Email Address</div>
<div class="field" style="left:867px;top:3593px;width:183px">Phone Number</div>
<div class="field" style="left:665px;top:3666px;width:385px">Select Subject</div>
<div class="field" style="left:665px;top:3739px;width:385px">dd/mm/yyyy</div>
<div class="abs" style="left:665px;top:3812px;width:385px;height:52px;background:var(--green);color:#fff;font-weight:700;font-size:18px;display:flex;align-items:center;justify-content:center">SUBMIT</div>

<!-- Clients review -->
<div class="abs" style="left:0;top:3925px;width:1200px;height:620px;background:var(--lavender)"></div>
<h2 class="section-title" style="top:4000px">Clients Review</h2>
<p class="section-sub" style="top:4067px">Lorem ipsum dolor sit amet, consectetur adipiscing elit, sed do eiusmod temp<br>or incididunt ut labore et dolore</p>

<div class="review-card" style="left:102px">
  <div class="avatar" role="img" aria-label="Client portrait"></div><div class="quote">”</div>
  <div class="stars">★★★★★</div>
  <p>Lorem ipsum dolor sit amet, consectetur adipiscing elit, sed do eiusmod or incididun t ut labore et dolore Lorem ipsum dolor sit adipiscing elit, sed do ehjhj</p>
  <h4>Tara Redsing</h4><small>BUSINESSMAN</small>
</div>
<div class="review-card" style="left:445px;border-bottom:4px solid var(--navy)">
  <div class="avatar" role="img" aria-label="Client portrait" style="background:linear-gradient(160deg,#f1ede6,#c9a27a 55%,#5e4636)"></div><div class="quote">”</div>
  <div class="stars">★★★★★</div>
  <p>Lorem ipsum dolor sit amet, consectetur adipiscing elit, sed do eiusmod or incididun t ut labore et dolore Lorem ipsum dolor sit adipiscing elit, sed do ehjhj</p>
  <h4>Tara Redsing</h4><small>BUSINESSMAN</small>
</div>
<div class="review-card" style="left:787px">
  <div class="avatar" role="img" aria-label="Client portrait" style="background:linear-gradient(160deg,#c9d3dc,#8a6e5c 50%,#2f3b48)"></div><div class="quote">”</div>
  <div class="stars">★★★★★</div>
  <p>Lorem ipsum dolor sit amet, consectetur adipiscing elit, sed do eiusmod or incididun t ut labore et dolore Lorem ipsum dolor sit adipiscing elit, sed do ehjhj</p>
  <h4>Tara Redsing</h4><small>BUSINESSMAN</small>
</div>

<!-- Footer -->
<div class="abs footer"></div>
<svg class="abs" style="left:0;top:4525px" width="1200" height="100" viewBox="0 0 1200 100"><path d="M0 0 H1200 V5 Q600 150 0 5Z" fill="var(--lavender)"/></svg>
<svg class="abs" style="left:240px;top:4590px" width="720" height="40" viewBox="0 0 720 40"><path d="M5 5 Q360 45 715 5" fill="none" stroke="var(--green)" stroke-width="3"/></svg>
<div class="abs" style="left:570px;top:4585px;width:60px;height:60px;border-radius:50%;background:#fff;display:flex;align-items:center;justify-content:center">
  <svg width="38" height="38" viewBox="0 0 40 40"><circle cx="20" cy="20" r="19" fill="var(--green)"/><path d="M14 13a10 10 0 1 0 12 0" fill="none" stroke="#fff" stroke-width="3" stroke-linecap="round"/><path d="M20 9v11" stroke="#fff" stroke-width="3" stroke-linecap="round"/></svg>
</div>
<div class="abs footer-brand">VoltaNix</div>
<nav class="footer-nav">
  <a style="left:333px">HOME</a>
  <a style="left:427px">SERVICES</a>
  <a style="left:533px">ABOUT US</a>
  <a style="left:652px">TESTIMONIALS</a>
  <a style="left:802px">BLOG</a>
</nav>
<div class="abs" style="left:140px;top:4880px;width:920px;height:1px;background:rgba(255,255,255,.3)"></div>
<div class="footer-contact" style="left:176px">
  <div class="ring"><svg width="26" height="26" viewBox="0 0 24 24" fill="none" stroke="#fff" stroke-width="1.3"><circle cx="12" cy="12" r="9"/><path d="M3 12h18M12 3c3 3 3 15 0 18M12 3c-3 3-3 15 0 18"/></svg></div>
  <div>123, Building Name, Street<br>City, State XY 123456</div>
</div>
<div class="abs" style="left:430px;top:4920px;width:1px;height:62px;background:rgba(255,255,255,.3)"></div>
<div class="footer-contact" style="left:508px">
  <div class="ring"><svg width="22" height="26" viewBox="0 0 20 26" fill="none" stroke="#fff" stroke-width="1.4"><rect x="3" y="1" width="14" height="24" rx="2"/><path d="M8 21h4"/></svg></div>
  <div>PHONE<br>(123) 456 7890</div>
</div>
<div class="abs" style="left:750px;top:4920px;width:1px;height:62px;background:rgba(255,255,255,.3)"></div>
<div class="footer-contact" style="left:831px">
  <div class="ring"><svg width="26" height="26" viewBox="0 0 24 24" fill="none" stroke="#fff" stroke-width="1.4"><rect x="3" y="6" width="18" height="13" rx="1"/><path d="M3 7l9 7 9-7"/></svg></div>
  <div>EMAIL<br>info@company.com</div>
</div>
<div class="abs bottom-bar"></div>
<div class="abs" style="left:147px;top:5033px;color:#fff;font-size:11px;font-weight:700">VoltaNix</div>
<div class="social" style="left:935px"></div>
<div class="social" style="left:967px"></div>
<div class="social" style="left:999px"></div>
<div class="social" style="left:1031px"></div>

</body>
</html>
```